HarborQuote - Webstartup looking for some style

HarborQuote is a cloud based web application that allows construction sub-contractors to create and manage bids. Generally, these contractors will contact subcontractors to have them do specific parts of a larger construction project. This would be used by various subcontractors including woodwork (cabinetry), electricians, masons, etc...

Nearly all competitors are clients applications that have to be installed on the computer and are very expensive. This is a much lower cost alternative.

The business is just beginning and we want people to view us as a fresh alternative to companies that have been around for a long time and are starting to look a little dated.

We would like our logo included on the card (see attached). We have been using the circular 'hq' emblem seperately from the complete logo in various areas of the website. We lean towards a professional and clean look, with a tendancy more towards modern.

We want to differentiate ourselves from our competition which tend to be dated, complicated and less graphical.

(We are currently designing our public website as well - but don't have any designs yet)

Industry/Entity Type

Construction

Requirements
Must have
• Circular 'hq' emblem from logo. Probably entire logo, but not necessarily.

Should have reference to website: www.harborquote-example.com

The Url should be all lowercase (www.harborquote-example.com)
Should not have
• we do not want to list a phone number or email address on the cards. we want people to go to the actual website. we haven't decided if we want names printed on the business cards.

```html
<!DOCTYPE html>
<html lang="en">
<head>
<meta charset="utf-8">
<title>HarborQuote Business Cards</title>
<link rel="stylesheet" href="https://fonts.googleapis.com/css2?family=Didact+Gothic&family=Roboto+Condensed:wght@700&display=swap">
<style>
  :root {
    --stage: #1f7fbf;
    --stage-deep: #124e78;
    --brand-blue: #1e88cc;
    --brand-orange: #f5961f;
    --orange-light: #f8b24c;
    --ink: #2a2a2a;
    --paper: #ffffff;
    --paper-shade: #e6e6e6;
    --name-light: #ececec;
  }
  * { box-sizing: border-box; margin: 0; padding: 0; }
  html, body {
    width: 1200px;
    height: 1200px;
    overflow: hidden;
  }
  body {
    background: radial-gradient(circle at 55% 50%, var(--stage) 0%, var(--stage-deep) 100%);
    position: relative;
    font-family: "Didact Gothic", sans-serif;
  }
  .card {
    position: absolute;
    left: 220px;
    width: 760px;
    height: 434px;
    overflow: hidden;
    box-shadow: 0 10px 24px rgba(0, 0, 0, 0.35);
  }

  /* Front */
  .card-front {
    top: 110px;
    background: linear-gradient(135deg, var(--paper-shade) 0%, var(--paper) 45%, var(--paper) 70%, var(--paper-shade) 100%);
  }
  .front-brand {
    position: absolute;
    top: 50px;
    left: 0;
    right: 0;
    text-align: center;
  }
  .brand-dot {
    display: block;
    width: 96px;
    height: 96px;
    margin: 0 auto 14px;
    border-radius: 50%;
    background: var(--brand-orange);
  }
  .front-name {
    font-size: 88px;
    font-weight: 400;
    line-height: 1;
    color: var(--brand-blue);
    letter-spacing: -1px;
  }
  .front-tagline {
    margin-top: 10px;
    font-family: "Roboto Condensed", sans-serif;
    font-weight: 700;
    font-size: 25px;
    color: var(--ink);
    letter-spacing: -0.3px;
  }
  .url-band {
    position: absolute;
    left: 0;
    right: 0;
    bottom: 40px;
    height: 64px;
    display: flex;
  }
  .url-band .band-blue { flex: 0 0 60%; background: var(--brand-blue); }
  .url-band .band-orange { flex: 1; background: var(--brand-orange); }
  .front-url {
    position: absolute;
    left: 0;
    right: 0;
    bottom: 48px;
    text-align: center;
    font-size: 38px;
    line-height: 48px;
    color: var(--ink);
    letter-spacing: 1px;
  }

  /* Back */
  .card-back {
    top: 650px;
    background: linear-gradient(120deg, var(--orange-light) 0%, var(--brand-orange) 55%, #e4841a 100%);
  }
  .back-band {
    position: absolute;
    top: 0;
    bottom: 0;
    left: 0;
    width: 200px;
    background: var(--brand-blue);
  }
  .back-text {
    position: absolute;
    right: 48px;
    bottom: 40px;
    text-align: right;
    color: var(--name-light);
  }
  .back-name {
    font-size: 62px;
    font-weight: 400;
    line-height: 1;
  }
  .back-tagline {
    margin-top: 6px;
    font-family: "Roboto Condensed", sans-serif;
    font-weight: 700;
    font-size: 18px;
  }
  .back-url {
    margin-top: 16px;
    font-size: 32px;
    letter-spacing: 1px;
  }
</style>
</head>
<body>
  <section class="card card-front">
    <div class="front-brand">
      <span class="brand-dot"></span>
      <h1 class="front-name">HarborQuote</h1>
      <p class="front-tagline">Smarter Bids for Specialty Trades</p>
    </div>
    <div class="url-band"><span class="band-blue"></span><span class="band-orange"></span></div>
    <p class="front-url">www.harborquote-example.com</p>
  </section>

  <section class="card card-back">
    <div class="back-band"></div>
    <div class="back-text">
      <h2 class="back-name">HarborQuote</h2>
      <p class="back-tagline">Smarter Bids for Specialty Trades</p>
      <p class="back-url">www.harborquote-example.com</p>
    </div>
  </section>
</body>
</html>
```